Graphic design for "How It Works" for VelmoraAttire.net*

VelmoraAttire.net website is for selling custom designer outfits for women and girls in all countries, customers can choose existing designs on this website and customize to their measurements. Customers can also provide their own designs and measurements and our expert designers and tailors get the outfit stitched and delivered to the customer.

We wanted to explain how this entire process works in 4 steps in the form of graphic design with little heading and text describing each step.

Step 1: Select Dress
Its time to choose the beauty you want to adorn yourself with. We have a wide collection of premium dresses, colours and accessories. There is something for everyone! All you need to do is pick. If you can’t find what you are looking for then you can share a picture of what you want, we will get it done whatever you want.

Step 2: Customization
Everyone is different; hence we realise the need for customization of the design and size. Here you select exactly how you want your dress to be. From sleeves to cuts, everything will be done as per your wish. Enter your measurements, lo and behold! You’re done. Leave your comments for even more customization.

Step 3: Designer Consultation
We as a user-friendly brand, aspire to provide the best of services to our clients. Our expert lady designers will help you for everything right from selecting of fabric to design of dress to necessary accessories. Our designers are just a call away!

Step 4: Stitch and Deliver
After you have placed your order, we confirm and verify the details. The boutique completes your order, sends it to us and we deliver it to your doorstep. We also have a team of designers in-house to cater to your premium dressing needs.

```html
<!DOCTYPE html>
<html lang="en">
<head>
<meta charset="utf-8">
<title>VelmoraAttire.net – How It Works</title>
<link rel="stylesheet" href="https://fonts.googleapis.com/css2?family=Poppins:ital,wght@0,500;1,600&family=Merriweather:wght@300&display=swap">
<style>
  :root {
    --pink: #c9467f;
    --pink-dark: #9c2f5f;
    --pink-soft: #e7a6c4;
    --ink: #2f3038;
    --ink-dark: #1c1d23;
    --text: #3a3a3a;
    --grey: #dcd9dc;
    --paper: #ffffff;
    --box: #f7f7f7;
  }
  * { margin: 0; padding: 0; box-sizing: border-box; }
  html, body { width: 1200px; height: 370px; overflow: hidden; background: var(--paper); }
  .canvas { position: relative; width: 1200px; height: 370px; overflow: hidden; }
  .corner { position: absolute; }
  .corner-top-left { left: 0; top: 0; }
  .corner-bottom-right { right: 0; bottom: 0; }
  .corner-bottom-left { left: 0; bottom: 0; }
  .corner-top-right { right: 0; top: 0; }

  .step { position: absolute; top: 0; width: 290px; height: 370px; }
  .step-art {
    position: absolute; top: 14px; left: 0; width: 240px; height: 166px;
    border-radius: 50% 50% 46% 46% / 30% 30% 70% 70%;
    background: radial-gradient(ellipse at 50% 70%, var(--grey) 0%, #e9e5e8 55%, #f6eef2 100%);
  }
  .step-art::after {
    content: ""; position: absolute; left: 30%; top: 18%; width: 40%; height: 48%;
    border-radius: 8px; background: linear-gradient(160deg, #f3d3e1, var(--pink-soft));
    opacity: .7;
  }
  .step-box {
    position: absolute; top: 217px; width: 178px; height: 98px;
    background: var(--box);
    box-shadow: 0 1px 4px rgba(0,0,0,.18);
    padding: 14px 9px 6px 10px;
    z-index: 1;
  }
  .step-box p {
    font-family: "Merriweather", serif; font-weight: 300;
    font-size: 7.6px; line-height: 9.75px; color: var(--text);
    text-align: justify;
  }
  .step-tab {
    position: absolute; top: 200px; width: 130px; height: 24px;
    border-radius: 10px 14px 14px 0;
    font-family: "Poppins", sans-serif; font-weight: 500; font-size: 8px;
    color: #fff; line-height: 24px; padding-left: 7px;
    white-space: nowrap; overflow: visible; z-index: 2;
  }
  .step-tab em { font-style: italic; font-weight: 600; }
  .step-tab::after {
    content: ""; position: absolute; left: 0; top: 24px;
    border-top: 6px solid; border-left: 6px solid transparent;
    border-top-color: inherit;
  }
  .tab-pink { background: var(--pink); border-color: var(--pink-dark); }
  .tab-ink { background: var(--ink); border-color: var(--ink-dark); }
  .step-number {
    position: absolute; top: 325px; width: 37px; height: 37px; border-radius: 50%;
    font-family: "Poppins", sans-serif; font-weight: 600; font-size: 26px;
    color: #fff; text-align: center; line-height: 38px;
    background: var(--pink); box-shadow: 2px 2px 0 var(--ink);
  }
</style>
</head>
<body>
<main class="canvas">
  <svg class="corner corner-top-left" width="140" height="95" viewBox="0 0 140 95" aria-hidden="true">
    <path d="M0 0 H135 C80 8 30 30 0 90 Z" fill="var(--pink)"/>
    <circle cx="48" cy="22" r="18" fill="#d45e93" opacity=".6"/>
  </svg>
  <svg class="corner corner-bottom-right" width="150" height="100" viewBox="0 0 150 100" aria-hidden="true">
    <path d="M150 0 V100 H15 C80 92 130 60 150 0 Z" fill="var(--pink)"/>
    <circle cx="128" cy="78" r="18" fill="#d45e93" opacity=".6"/>
  </svg>
  <svg class="corner corner-bottom-left" width="20" height="14" viewBox="0 0 20 14" aria-hidden="true">
    <path d="M0 0 C10 0 18 6 18 14 H0 Z" fill="var(--pink)"/>
  </svg>
  <svg class="corner corner-top-right" width="20" height="8" viewBox="0 0 20 8" aria-hidden="true">
    <path d="M20 0 V8 C10 8 4 4 2 0 Z" fill="var(--pink)"/>
  </svg>

  <section class="step" style="left:47px">
    <div class="step-art" role="img" aria-label="Illustration: a woman choosing a dress from a grid of outfits on a laptop screen"></div>
    <h2 class="step-tab tab-pink" style="left:16px"><em>STEP 1:</em> Select Dress</h2>
    <div class="step-box" style="left:22px"><p>Its time to choose the beauty you want to adorn yourself with. We have a wide collection of premium dresses, colours and accessories. There is something for everyone! All you need to do is pick. If you can’t find what you are looking for then you can share a picture of what you want, we will get it done whatever you want.</p></div>
    <div class="step-number" style="left:92px">1</div>
  </section>

  <section class="step" style="left:345px">
    <div class="step-art" role="img" aria-label="Illustration: a woman customizing a red dress on a laptop with garment options floating around"></div>
    <h2 class="step-tab tab-ink" style="left:11px"><em>STEP 2:</em> Customization</h2>
    <div class="step-box" style="left:17px"><p>Everyone is different; hence we realise the need for customization of the design and size. Here you select exactly how you want your dress to be. From sleeves to cuts, every-thing will be done as per your wish. Enter your measurements, lo and behold! You’re done. Leave your comments for even more customization.</p></div>
    <div class="step-number" style="left:88px">2</div>
  </section>

  <section class="step" style="left:647px">
    <div class="step-art" role="img" aria-label="Illustration: a designer at her desk chatting by phone with a customer about a dress"></div>
    <h2 class="step-tab tab-pink" style="left:7px"><em>STEP 3:</em> Designer Consultation</h2>
    <div class="step-box" style="left:13px"><p>We as a user-friendly brand, aspire to provide the best of services to our clients. Our expert lady designers will help you for everything right from selecting of fabric to design of dress to necessary accessories. Our designers are just a call away!</p></div>
    <div class="step-number" style="left:83px">3</div>
  </section>

  <section class="step" style="left:935px">
    <div class="step-art" role="img" aria-label="Illustration: tailors stitching at workbenches and a courier handing a parcel to a customer"></div>
    <h2 class="step-tab tab-ink" style="left:19px"><em>STEP 4:</em> Stitch And Deliver</h2>
    <div class="step-box" style="left:25px"><p>After you have placed your order, we confirm and verify the details. The boutique completes your order, sends it to us and we deliver it to your doorstep. We also have a team of designers in-house to cater to your customization.</p></div>
    <div class="step-number" style="left:96px">4</div>
  </section>
</main>
</body>
</html>
```